Gardener needs an exciting new flyer design.

I'm a passionate gardener that requires a custom flyer design for a owner operator gardening business. Design will be for a DL flyer. I'm based on the Sunshine coast in Queensland Australia. My target audience is the residential market on the Sunshine coast. Business name is Marlowe Grove. My services are, lawn mowing, weeding, Eco Friendly fertilizing, green waste removal, Mulching, tree and shrub pruning, Full garden makeovers, hedging, pressure cleaning, privacy screening, Timber deck rejuvenation, Planting, Turf preparation and installation, and much more. Free no obligation quotes, reliable and friendly service, great rates. 12 years experience. Web www.marlowegrove.com.au - Phone 0481527306 - Email tom@marlowegrove.com.au I would like the design to portray a friendly and professional approach.

Target Market(s)

Residential

Industry/Entity Type

Gardener

Font styles to use
Serif

Colors
9ccb3b
abd037
3176b5

Requirements
Must have
• my services, my logo, my contact details,

```html
<!DOCTYPE html>
<html lang="en">
<head>
<meta charset="utf-8">
<title>Marlowe Grove – DL Flyer</title>
<link rel="stylesheet" href="https://fonts.googleapis.com/css2?family=Oswald:wght@400;600&family=Alegreya:wght@400;700&display=swap">
<style>
  :root {
    --backdrop: #e4e4e4;
    --leaf: #3e7a37;
    --leaf-deep: #2f6329;
    --paper: #ffffff;
    --ink-light: #f4f8ef;
    --ink-green: #3e7a37;
    --photo-sky: #dfe9d2;
    --photo-foliage: #5d7f3c;
    --photo-shade: #2f4a22;
  }
  * { box-sizing: border-box; margin: 0; padding: 0; }
  html, body { width: 1200px; height: 901px; overflow: hidden; }
  body { background: var(--backdrop); position: relative; font-family: "Alegreya", Georgia, serif; }

  .flyer {
    position: absolute; left: 50px; top: 191px;
    width: 1100px; height: 519px;
    background: var(--leaf); overflow: hidden;
    box-shadow: 0 18px 40px rgba(0,0,0,.18);
  }

  .garden-photo { position: absolute; left: 0; top: 0; width: 1100px; height: 449px; }

  .brand { position: absolute; left: 40px; top: 26px; display: flex; align-items: center; gap: 14px; }
  .brand-mark { width: 44px; height: 44px; border-radius: 50%; background: var(--ink-light); }
  .brand-name { font-family: "Alegreya", Georgia, serif; font-weight: 700; font-size: 32px; line-height: 1; color: var(--ink-light); }

  .brand-intro {
    position: absolute; left: 40px; top: 84px; width: 430px;
    font-size: 14.5px; line-height: 1.35; color: var(--ink-light);
  }

  .promises { position: absolute; left: 40px; top: 146px; list-style: none; }
  .promises li {
    font-family: "Oswald", Arial, sans-serif; text-transform: uppercase;
    font-size: 15px; letter-spacing: .5px; color: var(--ink-light);
    display: flex; align-items: center; gap: 8px; line-height: 1.55;
  }
  .promises svg { width: 16px; height: 16px; }

  .services-title {
    position: absolute; left: 40px; top: 230px;
    border: 2px solid var(--ink-light); padding: 2px 16px;
    font-family: "Oswald", Arial, sans-serif; font-size: 19px; line-height: 1.4; letter-spacing: 1px;
    color: var(--ink-light); text-transform: uppercase;
  }
  .services { position: absolute; left: 40px; top: 278px; display: flex; gap: 36px; }
  .services ul { list-style: none; }
  .services li { font-size: 14.5px; line-height: 1.35; color: var(--ink-light); white-space: nowrap; }
  .services li::before { content: "· "; }

  .headline {
    position: absolute; right: 40px; top: 36px; text-align: right;
    font-family: "Oswald", Arial, sans-serif; font-weight: 600; text-transform: uppercase;
    color: var(--paper); font-size: 34px; line-height: 1.1;
    text-shadow: 0 2px 6px rgba(0,0,0,.45);
  }

  .contact-strip {
    position: absolute; left: 0; bottom: 0; width: 1100px; height: 70px;
    background: var(--paper); display: flex; align-items: center; gap: 30px; padding-left: 40px;
    font-family: "Oswald", Arial, sans-serif; color: var(--ink-green);
  }
  .contact-strip .cta { font-size: 26px; font-weight: 600; text-transform: uppercase; letter-spacing: .5px; }
  .contact-strip .details { font-size: 18px; letter-spacing: .5px; }

  .quote-badge { position: absolute; right: 40px; bottom: 18px; width: 170px; height: 170px; }
  .quote-badge text { font-family: "Oswald", Arial, sans-serif; font-weight: 600; fill: var(--paper); font-size: 19px; text-transform: uppercase; }
</style>
</head>
<body>
  <main class="flyer">
    <svg class="garden-photo" viewBox="0 0 1100 449" role="img" aria-label="Photograph of a lush front garden with white daisies, clipped hedges and a house behind trees">
      <defs>
        <linearGradient id="gardenTones" x1="0" y1="0" x2="0.4" y2="1">
          <stop offset="0" stop-color="var(--photo-sky)"/>
          <stop offset="0.35" stop-color="var(--photo-foliage)"/>
          <stop offset="1" stop-color="var(--photo-shade)"/>
        </linearGradient>
      </defs>
      <path d="M560 0 H1100 V449 H500 C470 330 470 160 560 0 Z" fill="url(#gardenTones)"/>
    </svg>

    <div class="brand">
      <span class="brand-mark"></span>
      <span class="brand-name">Marlowe Grove</span>
    </div>
    <p class="brand-intro">Marlowe Grove is a local owner operated garden care business servicing Sunshine Coast homes with friendly, reliable and affordable work done right.</p>

    <ul class="promises">
      <li><svg viewBox="0 0 16 16"><path d="M2 8.5 L6 12.5 L14 3.5" fill="none" stroke="var(--ink-light)" stroke-width="2.4"/></svg>Reliable and friendly service</li>
      <li><svg viewBox="0 0 16 16"><path d="M2 8.5 L6 12.5 L14 3.5" fill="none" stroke="var(--ink-light)" stroke-width="2.4"/></svg>12 years experience</li>
      <li><svg viewBox="0 0 16 16"><path d="M2 8.5 L6 12.5 L14 3.5" fill="none" stroke="var(--ink-light)" stroke-width="2.4"/></svg>Great rates</li>
    </ul>

    <h2 class="services-title">Our Services</h2>
    <div class="services">
      <ul>
        <li>Pressure cleaning</li>
        <li>Eco friendly fertilizing</li>
        <li>Green waste removal</li>
        <li>Tree and shrub pruning</li>
        <li>Full garden makeovers</li>
        <li>Timber deck rejuvenation</li>
        <li>Turf preparation and install</li>
      </ul>
      <ul>
        <li>Lawn mowing</li>
        <li>Weeding</li>
        <li>Mulching</li>
        <li>Hedging</li>
        <li>Privacy screening</li>
        <li>Planting</li>
        <li>and much more</li>
      </ul>
    </div>

    <h1 class="headline">A beautiful garden<br>doesn't happen by itself</h1>

    <footer class="contact-strip">
      <span class="cta">Book an appointment</span>
      <span class="details">0481527306 &nbsp;|&nbsp; www.marlowegrove.com.au &nbsp;|&nbsp; tom@marlowegrove.com.au</span>
    </footer>

    <svg class="quote-badge" viewBox="0 0 170 170">
      <polygon fill="var(--leaf)" points="85,2 97,22 118,9 121,33 145,28 139,51 163,56 150,75 168,90 148,102 160,123 136,126 138,150 115,144 106,167 89,150 72,167 63,144 40,150 42,126 18,123 30,102 10,90 28,75 15,56 39,51 33,28 57,33 60,9 81,22"/>
      <text x="85" y="66" text-anchor="middle">Free no</text>
      <text x="85" y="90" text-anchor="middle">obligation</text>
      <text x="85" y="114" text-anchor="middle">quotes</text>
    </svg>
  </main>
</body>
</html>
```